AnswerCraft Website Redesign

I'm looking to redesign our website AnswerCraft.com. The main goal is to give it a fresh design that is easy on the eyes and pushes the users to creating an account.

Our platform is very simple and we only do one thing, we use ai to generate response to customer and product reviews.

See attached file to see the pricing section style.

On the homepage just under the hero section, I would like to include the wording:
"Write replies to the reviews you get on sites like:" then show the logos like we have on our register page: https://app.answercraft.com/public/index.php

Target Market(s)

Business owners with brick and morter business or any business or product that gets online reviews

Industry/Entity Type

reputation management

Number of Pages Required

2 page

Requirements
Must have
• Home page and pricing page

```html
<!DOCTYPE html>
<html lang="en">
<head>
<meta charset="utf-8">
<title>AnswerCraft — AI replies to your customer reviews</title>
<link href="https://fonts.googleapis.com/css2?family=Lato:wght@400;700;900&family=Roboto:wght@400;500;700&family=Merriweather:wght@400&family=Poppins:wght@500&display=swap" rel="stylesheet">
<style>
:root{
  --blue:#1f3f9e;
  --blue-dark:#1b3687;
  --band:#3d5fb0;
  --yellow:#f5c518;
  --orange:#f7a31b;
  --ink:#111;
  --muted:#666;
  --line:#c9c9c9;
  --soft:#f4f6fb;
  --green:#39b54a;
}
*{box-sizing:border-box;margin:0;padding:0}
html,body{width:1200px;height:3347px;overflow:hidden}
body{position:relative;background:#fff;font-family:'Lato',sans-serif;color:var(--ink)}
.abs{position:absolute}
a{color:inherit;text-decoration:none}

/* header */
.site-header{position:absolute;left:0;top:0;width:1200px;height:86px;background:#fff;box-shadow:0 2px 8px rgba(0,0,0,.06)}
.brand{position:absolute;left:112px;top:22px;display:flex;align-items:center;gap:10px}
.brand-mark{width:36px;height:36px;background:var(--blue);border-radius:6px}
.brand-name{font:900 30px 'Lato',sans-serif;color:var(--blue)}
.main-nav{position:absolute;left:442px;top:31px;display:flex;gap:38px;font:400 17px 'Lato',sans-serif}
.main-nav .active{color:var(--blue);text-decoration:underline;font-weight:700}
.btn{display:inline-flex;align-items:center;justify-content:center;border-radius:6px;font-weight:700}
.btn-blue{background:var(--blue);color:#fff}
.header-cta{position:absolute;left:952px;top:20px;width:136px;height:46px;font-size:17px}

/* hero */
.hero{position:absolute;left:0;top:86px;width:1200px;height:511px;background:linear-gradient(180deg,#fff 0%,#fafafa 100%)}
.hero-title-sm{position:absolute;left:110px;top:118px;font:700 38px 'Lato',sans-serif}
.hero-title{position:absolute;left:110px;top:168px;font:900 49px 'Lato',sans-serif}
.hero-text{position:absolute;left:112px;top:236px;width:440px;font:400 16.5px/1.8 'Merriweather',serif;color:#333}
.hero-btn1{position:absolute;left:112px;top:314px;width:154px;height:55px;font-size:19px}
.hero-btn2{position:absolute;left:287px;top:314px;width:112px;height:55px;font-size:19px;background:var(--yellow);color:#222}
.hero-photo{position:absolute;left:645px;top:24px;width:442px;height:458px;background:linear-gradient(160deg,#2a4db5,#1a3690);border-radius:30px}
.hero-badge{position:absolute;left:572px;top:72px;width:180px;height:64px;background:#fff;border-radius:6px;box-shadow:0 4px 14px rgba(0,0,0,.1)}
.hero-badge .dot{position:absolute;left:10px;top:12px;width:40px;height:40px;border-radius:50%;background:#f0c48a}
.hero-badge b{position:absolute;left:64px;top:13px;font:700 12px 'Lato',sans-serif}
.hero-badge small{position:absolute;left:64px;top:31px;font:400 8px 'Lato',sans-serif;color:#888}
.hero-badge i{position:absolute;left:64px;top:44px;font-style:normal;font-size:9px;color:var(--orange)}
.plus{position:absolute;font:900 20px 'Lato',sans-serif;line-height:1}

/* section headings */
.sec-title{position:absolute;left:0;width:1200px;text-align:center;font:700 38px 'Lato',sans-serif}
.sec-title em{font-style:normal;color:var(--blue)}
.rule{position:absolute;width:50px;height:3px;background:var(--line);left:575px}
.sites{position:absolute;left:90px;top:718px;width:1020px;display:flex;justify-content:space-between;font:700 28px 'Lato',sans-serif;color:#8a8a8a}

/* steps */
.step{position:absolute;width:300px;text-align:center}
.step-icon{width:114px;height:114px;border-radius:50%;background:#fff;box-shadow:0 8px 22px rgba(0,0,0,.12);margin:0 auto;display:flex;align-items:center;justify-content:center}
.step h3{margin-top:32px;font:700 20px 'Lato',sans-serif;color:var(--blue)}
.step p{margin-top:14px;font:400 14.5px/1.72 'Lato',sans-serif;color:var(--muted)}

/* feature cards */
.feature{position:absolute;top:1201px;width:337px;height:356px;background:#fff;box-shadow:0 4px 16px rgba(0,0,0,.12);text-align:center;font-family:'Roboto',sans-serif}
.feature h4{margin-top:30px;font:500 16px 'Roboto',sans-serif}
.feature p{margin:18px 18px 0;font:700 8.5px/1.7 'Roboto',sans-serif;color:#333}
.feature .art{position:absolute;left:30px;right:30px;top:112px;bottom:20px;border-radius:20px}
.view-more{position:absolute;left:523px;top:1601px;width:154px;height:55px;font-size:19px}

/* band */
.cta-band{position:absolute;left:0;top:1714px;width:1200px;height:312px;background:var(--band);color:#fff;text-align:center}
.cta-band h2{position:absolute;left:0;width:100%;top:52px;font:700 38px 'Lato',sans-serif}
.cta-band .rule{background:#fff;top:114px}
.cta-band p{position:absolute;left:0;width:100%;top:146px;font:700 16px 'Lato',sans-serif}
.cta-band .btn{position:absolute;left:523px;top:196px;width:154px;height:55px;background:var(--orange);color:#222;font-size:19px}

/* pricing */
.plan{position:absolute;top:2212px;height:675px;background:#fff;border-radius:16px;box-shadow:0 6px 24px rgba(0,0,0,.1);font-family:'Roboto',sans-serif;overflow:hidden}
.plan h4{text-align:center;font:500 19px 'Roboto',sans-serif;margin-top:30px}
.plan .sub{text-align:center;font-size:13px;color:#333;margin-top:12px}
.plan .hr{height:1px;background:#ddd;margin:14px 16px 0}
.plan .desc{text-align:center;font-size:13px;line-height:1.8;color:#333;margin:12px 16px 0}
.plan .go{position:absolute;left:15px;right:15px;height:44px;background:var(--blue);color:#fff;font:500 16px 'Roboto',sans-serif;display:flex;align-items:center;justify-content:center}
.feat-list{position:absolute;left:16px;list-style:none;font-size:13px;color:#222}
.feat-list li{display:flex;align-items:center;gap:14px;height:36px}
.feat-list li::before{content:"";width:10px;height:5px;border-left:2px solid var(--green);border-bottom:2px solid var(--green);transform:rotate(-45deg);margin-top:-3px}
.feat-head{position:absolute;left:16px;font:500 14px 'Roboto',sans-serif}
.see-all{position:absolute;left:16px;font-size:11px;color:#222}

/* footer */
.site-footer{position:absolute;left:0;top:2962px;width:1200px;height:385px;background:var(--blue-dark);color:#fff}
.foot-brand{position:absolute;left:112px;top:78px;display:flex;align-items:center;gap:14px}
.foot-brand .brand-mark{width:46px;height:46px;background:#fff}
.foot-brand span{font:900 40px 'Lato',sans-serif}
.foot-col{position:absolute;top:70px}
.foot-col h5{font:700 22px 'Lato',sans-serif;margin-bottom:18px}
.foot-col ul{list-style:none;font:400 15px 'Lato',sans-serif}
.foot-col li{height:34.5px;display:flex;align-items:center;gap:10px}
.foot-col li::before{content:"›";width:14px;height:14px;border-radius:50%;background:#fff;color:var(--blue-dark);font:900 12px/14px 'Lato',sans-serif;text-align:center}
.contact-row{display:flex;gap:14px;align-items:flex-start;font:400 15px/1.8 'Lato',sans-serif;margin-bottom:16px}
.contact-row .ic{width:32px;height:32px;border-radius:50%;background:#fff;flex:none;display:flex;align-items:center;justify-content:center}
.foot-line{position:absolute;left:112px;top:309px;width:976px;height:1px;background:rgba(255,255,255,.5)}
.copyright{position:absolute;left:0;width:1200px;top:337px;text-align:center;font:500 14px 'Poppins',sans-serif}
</style>
</head>
<body>

<header class="site-header">
  <a class="brand" href="#"><span class="brand-mark"></span><span class="brand-name">AnswerCraft</span></a>
  <nav class="main-nav">
    <a class="active" href="#">Home</a><a href="#">Why Reply?</a><a href="#">How It Works</a><a href="#">Pricing</a><a href="#">Blog</a>
  </nav>
  <a class="btn btn-blue header-cta" href="#">Contact Us</a>
</header>

<section class="hero">
  <h1 class="hero-title-sm">Welcome To</h1>
  <div class="hero-title">AnswerCraft</div>
  <p class="hero-text">It's simple. Our tool writes replies and responses to the reviews your customers leave.</p>
  <a class="btn btn-blue hero-btn1" href="#">Start for free</a>
  <a class="btn hero-btn2" href="#">Try Free</a>
  <div class="hero-photo" role="img" aria-label="Photo of a smiling woman making an OK hand gesture on a blue panel"></div>
  <div class="hero-badge"><span class="dot"></span><b>AnswerCraft</b><small>Replies made easy</small><i>★★★★★</i></div>
  <span class="plus" style="left:1146px;top:22px">+</span>
  <span class="plus" style="left:1146px;top:44px;color:var(--yellow)">+</span>
  <span class="plus" style="left:1146px;top:66px">+</span>
  <span class="plus" style="left:1146px;top:88px">+</span>
</section>

<h2 class="sec-title" style="top:628px">Write <em>replies to the reviews</em> you get on sites like</h2>
<div class="rule" style="top:686px"></div>
<div class="sites"><span>Searchly</span><span>Staynest</span><span>Starmark</span><span>Cartwell</span><span>Tripnote</span><span>Munchly</span><span>Craftory</span></div>

<h2 class="sec-title" style="top:812px">How it <em>works</em></h2>
<div class="rule" style="top:864px"></div>

<svg class="abs" style="left:330px;top:910px" width="540" height="110" viewBox="0 0 540 110" fill="none" stroke="#e4e4e4" stroke-width="10" stroke-linecap="round">
  <path d="M10 80 Q90 110 170 55"/><path d="M150 45 L178 52 L165 78" stroke-width="8"/>
  <path d="M370 40 Q440 -5 515 45"/><path d="M500 20 L520 50 L490 58" stroke-width="8"/>
</svg>

<div class="step" style="left:110px;top:898px">
  <div class="step-icon"><svg width="60" height="56" viewBox="0 0 60 56" fill="none" stroke="var(--blue)" stroke-width="2.5"><rect x="6" y="8" width="40" height="30" rx="2"/><path d="M2 44h48"/><circle cx="26" cy="20" r="5"/><path d="M17 34c2-6 16-6 18 0"/><circle cx="48" cy="10" r="8"/><path d="M44 10l3 3 5-6"/></svg></div>
  <h3>1 minute account creation</h3>
  <p>Gain access to the most powerful tool for writing unique and personal responses to the reviews your customers leave your business.</p>
</div>
<div class="step" style="left:450px;top:898px">
  <div class="step-icon"><svg width="56" height="56" viewBox="0 0 56 56" fill="none" stroke="var(--blue)" stroke-width="2.5"><rect x="8" y="14" width="30" height="38" rx="2"/><path d="M20 4h22l8 8v32H38"/><path d="M14 26h18M14 34h18M14 42h12"/></svg></div>
  <h3>We make it way too simple!</h3>
  <p>Just copy the customer review and paste it into your account dashboard.</p>
</div>
<div class="step" style="left:812px;top:898px">
  <div class="step-icon"><svg width="64" height="56" viewBox="0 0 64 56" fill="none" stroke="var(--blue)" stroke-width="2.5"><circle cx="20" cy="14" r="6"/><circle cx="32" cy="10" r="6"/><circle cx="44" cy="14" r="6"/><path d="M10 32c2-8 16-8 20-4M34 28c4-4 18-4 20 4"/><path d="M4 42h16l10 6h26"/><path d="M4 50h52"/></svg></div>
  <h3>Only a 10 second wait</h3>
  <p>In just seconds you'll receive 3 unique and personal responses. Choose the reply you like best or tell our system to generate 3 more.</p>
</div>

<article class="feature" style="left:45px">
  <h4>Improved SEO</h4>
  <p>Searchly loves seeing you leave a reply to your reviews and will give you a boost in their search results and local SEO.</p>
  <div class="art" role="img" aria-label="Illustration of a review card with a reply on a blue shape" style="background:linear-gradient(150deg,#2a4db5,#e6ecf8)"></div>
</article>
<article class="feature" style="left:431px">
  <h4>Build Customer Trust</h4>
  <p>Customers want to know there are humans behind your companies product or service. Show them you value their time.</p>
  <div class="art" role="img" aria-label="Illustration of a customer review and reply on a yellow diamond" style="background:linear-gradient(150deg,#f7b51b,#fff3cf)"></div>
</article>
<article class="feature" style="left:817px">
  <h4>Convert New Customers</h4>
  <p>FACT: Potential customers read reviews before making a decision. Give a good first impression with personalized replies.</p>
  <div class="art" role="img" aria-label="Illustration of a rental review with a personalized reply on a blue shape" style="background:linear-gradient(150deg,#2a4db5,#e6ecf8)"></div>
</article>

<a class="btn btn-blue view-more" href="#">View More</a>

<section class="cta-band">
  <h2>Ready to give AnswerCraft a try?</h2>
  <div class="rule"></div>
  <p>Get started today with one FREE Reply to your Review. No credit card required.</p>
  <a class="btn" href="#">Try For Free</a>
</section>

<h2 class="sec-title" style="top:2076px;line-height:41px">Never worry about having to <em>come up with a unique</em><br><em>response to each review</em> ever again!</h2>
<div class="rule" style="top:2170px"></div>

<div class="plan" style="left:186px;width:356px">
  <h4>Boss Mode</h4>
  <div class="sub">For individuals and small teams</div>
  <div class="hr"></div>
  <div class="desc">Harness the full power of AI writing with the ability to create full length content with full control &amp; flexibility.</div>
  <div class="hr"></div>
  <div class="abs" style="left:0;width:356px;top:186px;text-align:center;font:500 19px 'Roboto',sans-serif">$82/mo estimated</div>
  <div class="abs" style="left:16px;top:228px;font:700 12px 'Roboto',sans-serif">50K</div>
  <div class="abs" style="right:16px;top:228px;font:700 12px 'Roboto',sans-serif">700K+</div>
  <div class="abs" style="left:16px;top:253px;width:322px;height:5px;border-radius:3px;background:#dfe6f7"></div>
  <div class="abs" style="left:16px;top:253px;width:80px;height:5px;border-radius:3px;background:var(--blue)"></div>
  <div class="abs" style="left:86px;top:246px;width:18px;height:18px;border-radius:50%;background:#fff;border:2px solid var(--blue)"></div>
  <div class="abs" style="left:0;width:356px;top:280px;text-align:center;font:500 13px 'Roboto',sans-serif">100,000 words/mo</div>
  <a class="go" style="top:313px" href="#">Start Now</a>
  <div class="feat-head" style="top:410px">AI features individuals want:</div>
  <ul class="feat-list" style="top:436px"><li>50+ AI templates</li><li>Pagely Docs style editor</li><li>Penwise Chat</li><li>Compose &amp; command features</li><li>Live chat support</li></ul>
  <div class="see-all" style="top:628px">See all features</div>
</div>

<div class="plan" style="left:657px;width:353px">
  <div style="background:var(--soft);margin:0 10px;height:178px;padding-top:1px">
    <h4 style="margin-top:24px">Business</h4>
    <div class="sub">For growing teams and businesses</div>
    <div class="hr" style="margin:14px 6px 0"></div>
    <div class="desc" style="margin:12px 6px 0">Get custom words/user packages and billing options, and the onboarding and support you need to scale with Penwise.</div>
  </div>
  <div class="abs" style="left:0;width:353px;top:242px;text-align:center;font:500 17px 'Roboto',sans-serif">Custom Plan &amp; Price</div>
  <a class="go" style="top:313px" href="#">Start Now</a>
  <div class="abs" style="left:0;width:353px;top:366px;text-align:center;font-size:10px;color:#999">Get a personalized demo &amp; custom plan</div>
  <div class="feat-head" style="top:400px;left:28px;font-size:13px">AI features teams want:</div>
  <ul class="feat-list" style="top:424px;left:28px;font-size:12px"><li style="height:35px">Collaborate with more than 5 users</li><li style="height:35px">Tailored AI Brand Voice</li><li style="height:35px">API access (Coming soon)</li><li style="height:35px">Personalized onboarding &amp; training</li><li style="height:35px">Dedicated account manager</li></ul>
  <div class="see-all" style="top:614px;left:28px">See all features</div>
</div>

<footer class="site-footer">
  <div class="foot-brand"><span class="brand-mark"></span><span>AnswerCraft</span></div>
  <div class="foot-col" style="left:471px"><h5>Quick Links</h5>
    <ul><li>Home</li><li>About</li><li>How Its Work</li><li>Pricing</li><li>Contact Us</li></ul></div>
  <div class="foot-col" style="left:670px"><h5>Help Links</h5>
    <ul><li>FAQ</li><li>Terms of use</li><li>Privacy Policy</li><li>Support Links</li><li>Conditions</li></ul></div>
  <div class="foot-col" style="left:884px"><h5>Contact Us</h5>
    <div class="contact-row"><span class="ic"><svg width="14" height="18" viewBox="0 0 14 18"><path d="M7 0a7 7 0 0 0-7 7c0 5 7 11 7 11s7-6 7-11a7 7 0 0 0-7-7z" fill="var(--blue-dark)"/><circle cx="7" cy="7" r="2.5" fill="#fff"/></svg></span><span>AnswerCraft<br>United States</span></div>
    <div class="contact-row"><span class="ic"><svg width="16" height="16" viewBox="0 0 16 16"><path d="M3 1l3 3-2 2c1 2 3 4 5 5l2-2 3 3-2 3C7 15 1 9 1 3z" fill="var(--blue-dark)"/></svg></span><span style="line-height:32px">+1 555 010 2040</span></div>
    <div class="contact-row"><span class="ic"><svg width="16" height="12" viewBox="0 0 16 12"><rect width="16" height="12" rx="1" fill="var(--blue-dark)"/><path d="M1 1l7 6 7-6" stroke="#fff" fill="none" stroke-width="1.5"/></svg></span><span style="line-height:32px">info@answercraft.com</span></div>
  </div>
  <div class="foot-line"></div>
  <div class="copyright">Copyrights@2023.AnswerCraft.All Rights Reserved</div>
</footer>

</body>
</html>
```